VENTURE CAPITAL GROUP BUSINESS CARD DESIGN

Venture Capital Group based in SF looking for a bold business card design. No trendy colour explosion, 3D effects etc. Just "simple" optical effects. Works on your brain, keeps your eye focused and sticks to your mind.
Target Market(s)
Technology startups
Industry/Entity Type
Venture Capital
Contact Information for Business Card
DESMOND WHITLAKE
MANAGING PARTNER
187 FENWORTH ST SAN FRANCISCO, CA 94187
415.555.0142 O
415.555.0147 F
415.555.0193 C
desmond@veldtmoorcapital.ventures

```html
<!DOCTYPE html>
<html lang="en">
<head>
<meta charset="utf-8">
<title>Veldtmoor Capital Group — Business Card</title>
<link rel="stylesheet" href="https://fonts.googleapis.com/css2?family=Open+Sans:wght@400;600;700&display=swap">
<style>
  :root {
    --backdrop: #e6e8e6;
    --forest: #0f5a26;
    --leaf: #3dbb45;
    --paper: #ffffff;
    --ink-light: #ffffff;
    --orb: #e9ecea;
    --shadow: rgba(0, 0, 0, 0.18);
  }
  * { box-sizing: border-box; margin: 0; padding: 0; }
  html, body {
    width: 1200px; height: 900px; overflow: hidden;
    background: var(--backdrop);
    font-family: "Open Sans", Arial, sans-serif;
  }
  .canvas {
    position: relative; width: 1200px; height: 900px;
  }
  .card {
    position: absolute; left: 330px; width: 540px; height: 309px;
    border-radius: 18px; overflow: hidden;
    box-shadow: 0 14px 30px var(--shadow);
  }
  .card--front { top: 110px; background: var(--forest); }
  .card--back { top: 480px; background: var(--paper); }

  .brand {
    position: absolute; display: flex; flex-direction: column; align-items: center;
  }
  .brand__orb { border-radius: 50%; background: var(--orb); }
  .brand__name { font-weight: 600; letter-spacing: 2px; text-align: center; line-height: 1.2; }

  .card--front .brand { left: 0; right: 0; top: 62px; }
  .card--front .brand__orb { width: 104px; height: 104px; margin-bottom: 22px; }
  .card--front .brand__name { color: var(--ink-light); font-size: 26px; }

  .back__panel { position: absolute; inset: 0; width: 100%; height: 100%; }

  .card--back .brand { right: 36px; top: 62px; width: 200px; }
  .card--back .brand__orb { width: 82px; height: 82px; margin-bottom: 14px; }
  .card--back .brand__name { color: var(--forest); font-size: 17px; }

  .contact {
    position: absolute; left: 34px; top: 104px; color: var(--ink-light);
  }
  .contact__name { font-weight: 700; font-size: 23px; letter-spacing: 0.5px; line-height: 1.1; }
  .contact__role { color: var(--leaf); font-weight: 600; font-size: 13px; letter-spacing: 0.5px; margin-bottom: 6px; }
  .contact__address { font-size: 13px; line-height: 1.3; margin-bottom: 6px; }
  .contact__lines { list-style: none; font-size: 13.5px; line-height: 1.35; }
  .contact__lines li { display: flex; align-items: center; gap: 9px; }
  .contact__lines svg { width: 11px; height: 11px; flex: none; }
</style>
</head>
<body>
<main class="canvas">
  <section class="card card--front" aria-label="Card front">
    <div class="brand">
      <div class="brand__orb"></div>
      <p class="brand__name">VELDTMOOR<br>CAPITAL GROUP</p>
    </div>
  </section>

  <section class="card card--back" aria-label="Card back">
    <svg class="back__panel" viewBox="0 0 540 309" preserveAspectRatio="none" aria-hidden="true">
      <path d="M0 0 L190 0 C300 8 330 150 300 309 L0 309 Z" fill="var(--forest)"/>
      <path d="M190 0 C306 6 340 150 310 309" fill="none" stroke="var(--leaf)" stroke-width="4"/>
    </svg>

    <div class="contact">
      <h1 class="contact__name">DESMOND WHITLAKE</h1>
      <p class="contact__role">MANAGING PARTNER</p>
      <p class="contact__address">187 FENWORTH ST SAN<br>FRANCISCO, CA 94187</p>
      <ul class="contact__lines">
        <li><svg viewBox="0 0 12 12"><path d="M2 1 L4.5 1 L5.3 3.5 L3.9 4.6 C4.6 6 6 7.4 7.4 8.1 L8.5 6.7 L11 7.5 L11 10 C6 10.5 1.5 6 2 1 Z" fill="var(--leaf)"/></svg>415.555.0142</li>
        <li><svg viewBox="0 0 12 12"><rect x="2" y="4" width="8" height="6" rx="1" fill="var(--leaf)"/><rect x="3.5" y="1" width="5" height="3" fill="var(--leaf)"/></svg>415.555.0147</li>
        <li><svg viewBox="0 0 12 12"><rect x="3" y="1" width="6" height="10" rx="1" fill="none" stroke="var(--leaf)" stroke-width="1.3"/></svg>415.555.0193</li>
        <li><svg viewBox="0 0 12 12"><rect x="1" y="2.5" width="10" height="7" fill="none" stroke="var(--leaf)" stroke-width="1.2"/><path d="M1 2.5 L6 7 L11 2.5" fill="none" stroke="var(--leaf)" stroke-width="1.2"/></svg>desmond@veldtmoorcapital.ventures</li>
      </ul>
    </div>

    <div class="brand">
      <div class="brand__orb"></div>
      <p class="brand__name">VELDTMOOR<br>CAPITAL GROUP</p>
    </div>
  </section>
</main>
</body>
</html>
```